Business Card Design for Marketing Firm

Looking for business card design for higher end marketing firm. Clean but impressionable/trendy. We are a marketing firm that represents manufacturers in the foodservice equipment and supply industry. Our customers are end users such has hotels, restaurants, country clubs, convention centers and casinos as well as distributors of restaurants supplies and equipment, and manufacturers of foodservice equipment and supplies.
Target Market(s)
Hotels, Restaurants, Supply & Equipment Distributors, Foodservice Manufacturers
Industry/Entity Type
Foodservice/Hospitality
Contact Information for Business Card
Name, Title, Contact Number, Email, Website, Social Media, Address
Requirements
Must have
- Clean & Simple but Serious and Impressionable

```html
<!DOCTYPE html>
<html lang="en">
<head>
<meta charset="utf-8">
<title>Harbor Hospitality Reps – Business Card</title>
<link href="https://fonts.googleapis.com/css2?family=Cinzel:wght@600;700&family=Arimo:wght@400&display=swap" rel="stylesheet">
<style>
  :root {
    --navy: #0b0a78;
    --navy-deep: #08076a;
    --card-white: #f7f7f9;
    --ink: #1d1d24;
    --muted: #5f5f68;
    --rule: #2a2a33;
    --backdrop: #e4e4e8;
  }
  * { box-sizing: border-box; margin: 0; padding: 0; }
  html, body { width: 1200px; height: 960px; overflow: hidden; }
  body {
    background: var(--backdrop);
    font-family: "Arimo", Arial, sans-serif;
    position: relative;
  }
  .card {
    position: absolute;
    left: 320px;
    width: 560px;
    height: 320px;
    border-radius: 18px;
    box-shadow: 0 10px 28px rgba(0,0,0,.18);
    overflow: hidden;
  }
  .card-front { top: 110px; background: var(--card-white); color: var(--ink); }
  .card-back  { top: 530px; background: var(--navy); display: flex; align-items: center; justify-content: center; }

  .social { position: absolute; left: 26px; top: 22px; display: flex; gap: 5px; }
  .social span { width: 17px; height: 17px; border-radius: 50%; background: var(--navy); display: block; }

  .brand {
    position: absolute; right: 32px; top: 96px; text-align: right;
    font-family: "Cinzel", Georgia, serif; font-weight: 600; color: var(--navy);
  }
  .brand-name { font-size: 19px; letter-spacing: .5px; display: block; }
  .brand-rule { display: block; height: 1px; background: var(--navy); margin: 3px 0 2px; }
  .brand-sub { font-size: 12px; letter-spacing: 1px; display: block; }

  .person { position: absolute; left: 30px; top: 120px; }
  .person-name { font-family: "Cinzel", Georgia, serif; font-weight: 700; font-size: 23px; color: var(--navy); letter-spacing: .5px; }
  .person-title { font-size: 13px; color: var(--muted); margin-top: 2px; }

  .divider { position: absolute; left: 30px; right: 30px; top: 182px; height: 1px; background: var(--rule); }

  .contact { position: absolute; left: 30px; top: 194px; list-style: none; font-size: 13.5px; color: var(--ink); }
  .contact li { display: flex; align-items: center; gap: 8px; line-height: 20px; }
  .contact svg { width: 12px; height: 12px; fill: var(--navy); }

  .address { position: absolute; right: 32px; bottom: 30px; text-align: right; font-size: 14px; line-height: 19px; color: var(--ink); }

  .back-name {
    font-family: "Cinzel", Georgia, serif; font-weight: 600; color: #4a4ac4;
    font-size: 30px; letter-spacing: 2px; text-align: center; line-height: 1.25;
  }
</style>
</head>
<body>
  <section class="card card-front" aria-label="Card front">
    <div class="social" aria-label="Social media"><span></span><span></span><span></span></div>

    <div class="brand">
      <span class="brand-name">Harbor Hospitality</span>
      <span class="brand-rule"></span>
      <span class="brand-sub">Reps</span>
    </div>

    <div class="person">
      <h1 class="person-name">Daniel Reyes</h1>
      <p class="person-title">President</p>
    </div>

    <div class="divider"></div>

    <ul class="contact">
      <li>
        <svg viewBox="0 0 24 24" aria-hidden="true"><path d="M6.6 10.8a15 15 0 0 0 6.6 6.6l2.2-2.2a1 1 0 0 1 1-.25 11.4 11.4 0 0 0 3.6.57 1 1 0 0 1 1 1V20a1 1 0 0 1-1 1A17 17 0 0 1 3 4a1 1 0 0 1 1-1h3.5a1 1 0 0 1 1 1c0 1.25.2 2.45.57 3.57a1 1 0 0 1-.25 1z"/></svg>
        (555) 0142-7780
      </li>
      <li>
        <svg viewBox="0 0 24 24" aria-hidden="true"><path d="M2 5h20v14H2z M2 5l10 8 10-8" fill="none" stroke="#0b0a78" stroke-width="2"/><path d="M2 5h20L12 13z"/></svg>
        name@HARBOR.com
      </li>
    </ul>

    <address class="address" style="font-style:normal">
      4120 Linden Avenue<br>
      Brookvale, NY 10990
    </address>
  </section>

  <section class="card card-back" aria-label="Card back">
    <p class="back-name">Harbor Hospitality Reps</p>
  </section>
</body>
</html>
```